Business Cards for a law firm

Business cards for our law firm. Use our silhoette logo and OAK PARTNERS - check our website (www.oakpartners.example)

Contact Information for Business Card

our silhouette logo, OAK PARTNERS, 800-555-0147, Dorian Pemberton, dorian@oakpartners.example

Requirements
Must have
• our silhouette logo, OAK PARTNERS, 800-555-0147, Dorian Pemberton, dorian@oakpartners.example

```html
<!DOCTYPE html>
<html lang="en">
<head>
<meta charset="utf-8">
<title>Oak Partners – Business Cards</title>
<link href="https://fonts.googleapis.com/css2?family=Cinzel:wght@500;600&family=Arimo:wght@400&display=swap" rel="stylesheet">
<style>
  :root {
    --backdrop: #3c3c3c;
    --navy: #1b2f6b;
    --navy-soft: #243a7a;
    --paper: #ffffff;
    --ink-light: #ffffff;
  }
  * { box-sizing: border-box; margin: 0; padding: 0; }
  html, body { width: 1200px; height: 803px; overflow: hidden; }
  body {
    background: var(--backdrop);
    position: relative;
    font-family: "Arimo", Arial, sans-serif;
  }
  .card {
    position: absolute;
    top: 250px;
    width: 520px;
    height: 300px;
    border-radius: 22px;
    box-shadow: 0 14px 30px rgba(0,0,0,0.35);
    overflow: hidden;
  }
  .card--front { left: 50px; background: var(--navy); color: var(--ink-light); }
  .card--back  { left: 630px; background: var(--paper); color: var(--navy); }

  .firm-name {
    font-family: "Cinzel", serif;
    font-weight: 600;
    letter-spacing: 0.06em;
  }
  .card--front .firm-name {
    position: absolute; left: 40px; top: 58px;
    font-size: 22px;
  }
  .person-name {
    position: absolute; left: 40px; top: 148px;
    font-family: "Cinzel", serif; font-weight: 600;
    font-size: 19px; letter-spacing: 0.05em;
  }
  .contact-list {
    position: absolute; left: 40px; top: 196px;
    list-style: none; font-size: 13px; line-height: 19px;
  }
  .contact-list li { display: flex; align-items: center; gap: 8px; }
  .contact-list svg { width: 11px; height: 11px; fill: var(--ink-light); flex: none; }

  .artwork-area {
    position: absolute; right: 30px; top: 30px;
    width: 220px; height: 240px;
    background: linear-gradient(160deg, var(--navy-soft), var(--navy));
    border-radius: 6px;
  }

  .brand-lockup {
    position: absolute; left: 0; right: 0; top: 0; bottom: 0;
    display: flex; align-items: center; justify-content: center; gap: 14px;
  }
  .brand-mark { width: 26px; height: 26px; background: var(--navy); }
  .card--back .firm-name { font-size: 40px; }
</style>
</head>
<body>
  <section class="card card--front" aria-label="Card front">
    <h1 class="firm-name">OAK PARTNERS</h1>
    <p class="person-name">Dorian Pemberton</p>
    <ul class="contact-list">
      <li><svg viewBox="0 0 24 24" aria-hidden="true"><path d="M6.6 10.8a15 15 0 0 0 6.6 6.6l2.2-2.2a1 1 0 0 1 1-.25 11.4 11.4 0 0 0 3.6.57 1 1 0 0 1 1 1V20a1 1 0 0 1-1 1A17 17 0 0 1 3 4a1 1 0 0 1 1-1h3.5a1 1 0 0 1 1 1c0 1.25.2 2.45.57 3.57a1 1 0 0 1-.25 1z"/></svg>800-555-0147</li>
      <li><svg viewBox="0 0 24 24" aria-hidden="true"><path d="M2 5h20v14H2z M2 5l10 8 10-8" /></svg>dorian@oakpartners.example</li>
      <li><svg viewBox="0 0 24 24" aria-hidden="true"><circle cx="12" cy="12" r="10"/></svg>www.oakpartners.example</li>
    </ul>
    <div class="artwork-area" role="img" aria-label="Large white silhouette of two standing men"></div>
  </section>

  <section class="card card--back" aria-label="Card back">
    <div class="brand-lockup">
      <span class="brand-mark" aria-hidden="true"></span>
      <h2 class="firm-name">OAK PARTNERS</h2>
    </div>
  </section>
</body>
</html>
```